New Letterhead Design Project*

Target Market(s)

Corporate

Colors

Designer to choose colors to be used in the design.

Requirements
Must have
• An Overview / Background of the Business & Services- Company Name: ZAYN HALIMFOR CLEAR VENTURES W prefer as ZAYN HALIM. Zayn Halim offers specialized services in Network information security services, data center & Network infrastructure, data caption & security services, software services. Zayn Halim provides wide range of services that helps the organization in their business priorities strategies. Zayn Halim specialized team has handles prestigious projects & executed with ease.
• * The Target Market / Audience you are trying to reach – corporate We are doing CCTV supply & Service, cabling supply & Services , PI system supply & Service, BMS supply & Service, Fire & safety supply & services. we are basically target corporates ,malls, enterprise users and governments.
• * Design Specifics; any preferences or ideas for Style, Colour, Imagery, etc- We prefer mild & unique color.
Nice to have
• Mild and unique color

```html
<!DOCTYPE html>
<html lang="en">
<head>
<meta charset="utf-8">
<title>Zayn Halim Letterhead</title>
<link href="https://fonts.googleapis.com/css2?family=Open+Sans:wght@400;600;700&family=Source+Sans+3:wght@400;600&display=swap" rel="stylesheet">
<style>
  :root {
    --backdrop: #d6d6d8;
    --paper: #ffffff;
    --brand-blue: #2f9fd0;
    --band-deep: #3ea2ca;
    --band-light: #66c8ea;
    --ink: #3a3a3a;
    --ink-soft: #555555;
    --ink-muted: #6a6a6a;
  }
  * { margin: 0; padding: 0; box-sizing: border-box; }
  html, body {
    width: 1200px; height: 900px; overflow: hidden;
    background: var(--backdrop);
  }
  .letterhead {
    position: absolute; left: 270px; top: 26px;
    width: 660px; height: 848px;
    background: var(--paper);
    overflow: hidden;
    font-family: "Source Sans 3", sans-serif;
    color: var(--ink-soft);
  }
  .brand {
    position: absolute; left: 88px; top: 76px;
    display: flex; align-items: center; gap: 10px;
  }
  .brand-dot {
    width: 30px; height: 30px; border-radius: 50%;
    background: var(--brand-blue);
  }
  .brand-name {
    font-family: "Open Sans", sans-serif;
    font-weight: 400; font-size: 20px; line-height: 23px;
    color: var(--brand-blue); letter-spacing: 0.2px;
  }
  .contact-list {
    position: absolute; left: 478px; top: 56px;
    list-style: none; font-size: 8px; line-height: 10.5px; color: var(--ink-soft);
  }
  .contact-list li { display: flex; gap: 10px; margin-bottom: 6px; }
  .contact-list svg { width: 10px; height: 10px; flex: none; margin-top: 1px; }
  .recipient {
    position: absolute; left: 103px; top: 208px;
    font-size: 9.5px; line-height: 10.5px;
  }
  .recipient .to-label {
    position: absolute; left: -2px; top: -1px;
    font-family: "Open Sans", sans-serif; font-weight: 700; font-size: 11px; color: var(--ink);
  }
  .recipient .details { margin-left: 26px; }
  .recipient .name { font-family: "Open Sans", sans-serif; font-weight: 700; font-size: 9.5px; color: var(--ink); letter-spacing: 0.4px; }
  .recipient .role { font-family: "Open Sans", sans-serif; letter-spacing: 0.4px; margin-bottom: 14px; }
  .recipient .company { margin-top: 5px; }
  .letter-date {
    position: absolute; right: 103px; top: 208px;
    font-family: "Open Sans", sans-serif; font-weight: 600; font-size: 9.5px;
    color: var(--ink-soft); letter-spacing: 0.4px;
  }
  .letter-body {
    position: absolute; left: 103px; top: 342px; width: 454px;
  }
  .salutation {
    font-family: "Open Sans", sans-serif; font-weight: 700; font-size: 11.5px;
    color: var(--ink); letter-spacing: 0.6px; margin-bottom: 12px;
  }
  .letter-body p {
    font-size: 9.2px; line-height: 14.7px; text-align: justify;
    color: var(--ink-soft); margin-bottom: 12.5px;
  }
  .sign-off { position: absolute; left: 103px; top: 660px; font-size: 9.5px; }
  .signature {
    display: block; width: 170px; height: 36px; margin: 8px 0 9px 5px;
    background: linear-gradient(90deg, rgba(51,70,181,0.18), rgba(51,70,181,0.08));
    border-radius: 4px;
  }
  .signer-name { font-family: "Open Sans", sans-serif; font-weight: 700; font-size: 9.5px; color: var(--ink); }
  .signer-role { font-family: "Open Sans", sans-serif; font-size: 10px; color: var(--ink-muted); letter-spacing: 0.5px; margin-top: 3px; }
  .footer-band {
    position: absolute; left: 0; bottom: 0; width: 660px; height: 70px;
    background: linear-gradient(180deg, var(--band-light), var(--band-deep));
  }
</style>
</head>
<body>
  <main class="letterhead">
    <header class="brand">
      <span class="brand-dot"></span>
      <div class="brand-name">ZAYN HALIM FOR<br>CLEAR VENTURES</div>
    </header>

    <ul class="contact-list">
      <li>
        <svg viewBox="0 0 10 10"><rect x="1" y="1.5" width="8" height="5.5" rx="0.6" fill="none" stroke="var(--brand-blue)" stroke-width="1"/><rect x="3.5" y="8" width="3" height="1" fill="var(--brand-blue)"/></svg>
        <span>info@clearventures.net<br>www.clearventures.net</span>
      </li>
      <li>
        <svg viewBox="0 0 10 10"><path d="M2 1 L4 1 L4.6 3.2 L3.4 4.2 Q4.6 6.2 6 6.8 L7 5.6 L9 6.3 L9 8.3 Q4.5 8.8 1.5 3 Z" fill="var(--brand-blue)"/></svg>
        <span>001-555 310 472<br>001-555 310 473</span>
      </li>
      <li>
        <svg viewBox="0 0 10 10"><path d="M5 0.8 A3 3 0 0 1 8 3.8 C8 6 5 9.4 5 9.4 C5 9.4 2 6 2 3.8 A3 3 0 0 1 5 0.8 Z" fill="var(--brand-blue)"/><circle cx="5" cy="3.8" r="1.1" fill="#fff"/></svg>
        <span>Suite 4, Harbor Road, CA, USA<br>P.O. Box 7120 Westfield</span>
      </li>
    </ul>

    <section class="recipient">
      <span class="to-label">TO:</span>
      <div class="details">
        <div class="name">Marcus Ellery</div>
        <div class="role">HR Manager</div>
        <div>Suite 4, Harbor Road,</div>
        <div>CA, USA</div>
        <div>P.O. Box 7120</div>
        <div class="company">Northgate Logistics</div>
      </div>
    </section>

    <div class="letter-date">Date: 15/1/2006</div>

    <article class="letter-body">
      <h2 class="salutation">Dear Sir/Madam</h2>
      <p>Lorem ipsum dolor sit amet, consectetu er adipiscing elit. Aenean com modo ligula eg et dol or. Aenean massa. Cum sociis natoque penatibus et magnis dis parturient montes, nascetur ridiculus mus. Donec quam felis, ultricies nec, pellentesque eu, pretium quis, sem. Nu lla consequat massa quis enim. Donec pede justo, fringilla vel, aliquet nec, vul putate eget, arcu.</p>
      <p>In enim justo, rhoncus ut, imperdiet a, venenatis vitae, justo. Lorem ipsum dolor sit amet, consectetu er adipiscing elit. Aenean com modo ligula eget dolor. Aenean massa. Cum sociis natoque penatibus et magnis dis parturient montes, nascetur ridiculus mus. Donec quam felis, ultricies nec, pellentesque eu, pretium quis, sem. Nu lla consequat massa quis enim. Donec pede justo, fringilla vel, aliquet nec, vul putate eget, arcu. In enim justo, rhoncus ut, imperdiet a, venenatis vitae, justo.</p>
      <p>Lorem ipsum dolor sit amet, consectetu er adipiscing elit. Aenean com modo ligula eget dolor. Aenean massa. Cum sociis natoque penatibus et magnis dis parturient montes, nascetur ridiculus mus. Donec quam felis, ultricies nec,</p>
      <p>Lorem ipsum dolor sit amet, consectetu er adipiscing elit. Aenean com modo ligula eget dolor. Aenean massa. Cum sociis natoque penatibus et magnis dis parturient montes, nascetur ridiculus mus. Donec quam felis, ultricies nec, pellentesque eu, pretium quis, sem. Nu lla consequat massa quis enim.</p>
    </article>

    <footer class="sign-off">
      <div>Sincerley Yours</div>
      <span class="signature" role="img" aria-label="Handwritten signature of Owen Hartley"></span>
      <div class="signer-name">Owen Hartley</div>
      <div class="signer-role">Finance Manager</div>
    </footer>

    <div class="footer-band" role="img" aria-label="Decorative blue footer band"></div>
  </main>
</body>
</html>
```